Non fiction book cover. The book advises how to get a new job.

The book size will be 20cm high by 13cm wide and I need a front cover which can wrap around to the back. This book has a serious message, but I've tried to make it quite light to read and accessible. So I don't want a cover that is too dour or serious and not frivolous either. At the end of the project, I will need a high resolution 3D image of the book, included as part of the package.<br/>The Title of the book is:- "Past Sixty? Hunting for your final post?<br/>by Gareth Millbrook-Ashdown".<br/>I am thinking of a light yellow background, with a striking image to attract attention. The image and words should be clear and sharp.<br/>Here is the, BACK COVER wording.<br/>"This book tells you clearly and simply the steps that you need to take, to get a job, once you’re over 50.<br/>It advises you on the techniques to use to write a killer CV.<br/>It explains how to ensure that your CV attention.<br/>It shows the best way to approach your local job agency.<br/>It demonstrates the best way to use your network.<br/><br/>This book, written by someone with 30 years’ experience in the recruitment industry, gives you ALL the answers.<br/>Whether you are a top executive or someone after some local part time work, then this book is for you. <br/>With the help of this book you will secure your next position.<br/>

Target Market(s)

UK, over 50s, male and female.

Font styles to use
Serif

Colors
fbee3e

Requirements
Must have
• A clear uncluttered cover.
Should not have
• Fussy and over complicated

```html
<!DOCTYPE html>
<html lang="en">
<head>
<meta charset="utf-8">
<title>Past Sixty? Hunting for your final post? – Cover Wrap</title>
<link rel="stylesheet" href="https://fonts.googleapis.com/css2?family=Oswald:wght@600;700&family=Exo+2:wght@700;800&display=swap">
<style>
  :root {
    --cover-yellow: #fbee3e;
    --page-bg: #e6e6e4;
    --title-red: #d0141b;
    --ink: #141414;
    --outline: #ffffff;
    --compass-orange: #f2a33a;
    --compass-grey: #8c8172;
    --compass-face: #d9dde2;
    --compass-blue: #4d9fd6;
  }
  * { margin: 0; padding: 0; box-sizing: border-box; }
  html, body {
    width: 1200px; height: 960px; overflow: hidden;
    background: var(--page-bg);
  }
  .cover-wrap {
    position: absolute;
    left: 28px; top: 70px;
    width: 1144px; height: 819px;
    background: var(--cover-yellow);
    overflow: hidden;
    box-shadow: 0 6px 22px rgba(0,0,0,0.18);
  }
  .back-cover { position: absolute; left: 0; top: 0; width: 543px; height: 100%; }
  .spine { position: absolute; left: 543px; top: 0; width: 78px; height: 100%; }
  .front-cover { position: absolute; left: 621px; top: 0; width: 523px; height: 100%; }

  .blurb {
    position: absolute; left: 66px; top: 78px; width: 460px;
    font-family: "Exo 2", sans-serif; font-weight: 700;
    font-size: 12.5px; line-height: 23.5px; color: var(--ink);
  }
  .blurb p + p { margin-top: 23.5px; }

  .back-compass { position: absolute; left: 80px; top: 415px; }

  .outlined {
    text-shadow:
      -3px -3px 0 var(--outline), 3px -3px 0 var(--outline),
      -3px 3px 0 var(--outline), 3px 3px 0 var(--outline),
      0 -3px 0 var(--outline), 0 3px 0 var(--outline),
      -3px 0 0 var(--outline), 3px 0 0 var(--outline),
      5px 6px 0 #222;
  }

  .author {
    position: absolute; right: 112px; top: 34px;
    font-family: "Exo 2", sans-serif; font-weight: 800;
    font-size: 23px; letter-spacing: 0.5px; color: var(--ink);
  }
  .title {
    position: absolute; left: 42px; top: 100px;
    font-family: "Oswald", sans-serif; font-weight: 700;
    line-height: 1; transform: scaleX(0.86); transform-origin: left top;
  }
  .title-lead { display: block; font-size: 92px; color: var(--title-red); }
  .title-main { display: block; font-size: 72px; color: var(--ink); margin-top: 6px; }
  .title-rest { display: block; font-size: 50px; color: var(--ink); margin-top: 4px; white-space: nowrap; }

  .front-compass { position: absolute; left: 0; top: 0; }

  .spine-title {
    position: absolute; left: 39px; top: 409px;
    width: 708px; height: 60px; margin-left: -354px; margin-top: -30px;
    transform: rotate(-90deg);
    display: flex; align-items: center; justify-content: center; gap: 10px;
    font-family: "Oswald", sans-serif; font-weight: 700; white-space: nowrap;
  }
  .spine-lead { font-size: 46px; color: var(--title-red); }
  .spine-main { font-size: 40px; color: var(--ink); }
  .spine-rest { font-size: 28px; color: var(--ink); }
  .spine .outlined {
    text-shadow:
      -2px -2px 0 var(--outline), 2px -2px 0 var(--outline),
      -2px 2px 0 var(--outline), 2px 2px 0 var(--outline),
      3px 3px 0 #222;
  }
</style>
</head>
<body>
  <div class="cover-wrap">
    <section class="back-cover">
      <div class="blurb">
        <p>This book tells you clearly and simply the steps that<br>
        you need to take, to get a job, once you’re over 50.<br>
        It advises you on the techniques to use to write a killer CV.<br>
        It explains how to ensure that your CV attention.<br>
        It shows the best way to approach your local job agency.<br>
        It demonstrates the best way to use your network.</p>
        <p>This book, written by someone with 30 years’ experience<br>
        in the recruitment industry, gives you ALL the answers.<br>
        Whether you are a top executive or someone after some<br>
        local part time work, then this book is for you.<br>
        With the help of this book you will secure your next position.</p>
      </div>
      <svg class="back-compass" width="380" height="360" viewBox="0 0 380 360" role="img" aria-label="Faint compass illustration pointing to JOB">
        <defs>
          <radialGradient id="backCompassTone" cx="50%" cy="45%" r="55%">
            <stop offset="0%" stop-color="#b9df5a" stop-opacity="0.7"/>
            <stop offset="70%" stop-color="#f3e24a" stop-opacity="0.7"/>
            <stop offset="100%" stop-color="#f5c840" stop-opacity="0.6"/>
          </radialGradient>
        </defs>
        <ellipse cx="190" cy="180" rx="186" ry="172" fill="url(#backCompassTone)"/>
      </svg>
    </section>

    <section class="spine">
      <div class="spine-title">
        <span class="spine-lead outlined">Past Sixty?</span>
        <span class="spine-main outlined">Hunting</span>
        <span class="spine-rest outlined">for your final post?</span>
      </div>
    </section>

    <section class="front-cover">
      <svg class="front-compass" width="523" height="819" viewBox="0 0 523 819" role="img" aria-label="Illustrated compass with its needle pointing to JOB">
        <defs>
          <radialGradient id="frontCompassTone" cx="50%" cy="50%" r="50%">
            <stop offset="0%" stop-color="var(--compass-blue)"/>
            <stop offset="55%" stop-color="var(--compass-face)"/>
            <stop offset="78%" stop-color="var(--compass-grey)"/>
            <stop offset="100%" stop-color="var(--compass-orange)"/>
          </radialGradient>
        </defs>
        <circle cx="380" cy="705" r="340" fill="url(#frontCompassTone)"/>
      </svg>
      <div class="author">by Gareth Millbrook-Ashdown</div>
      <h1 class="title">
        <span class="title-lead outlined">Past Sixty?</span>
        <span class="title-main outlined">Hunting</span>
        <span class="title-rest outlined">for your final post?</span>
      </h1>
    </section>
  </div>
</body>
</html>
```